I will ask the design of the business card

We are looking for business card design of the new company "R DOVE PAYGRID WORKS LLC." Based in Azerbaijan.
In case
We are working on Azerbaijan to set up the first exchange of crypto currencies.

The key currency used in exchanges is called "PLUME".
In case
We are doing project to make crypto currency infrastructure.

We provide state-of-the-art technology to the world.

```html
<!DOCTYPE html>
<html lang="en">
<head>
<meta charset="utf-8">
<title>R Dove Paygrid Works LLC – Business Card</title>
<link rel="stylesheet" href="https://fonts.googleapis.com/css2?family=Open+Sans:wght@400;600&display=swap">
<style>
  :root {
    --stage: #202022;
    --card-dark: #19191a;
    --card-light: #ececec;
    --accent: #1d5e96;
    --ink: #4a4a4a;
    --ink-strong: #2e2e2e;
    --rule-dark: #5a5a5a;
    --rule-light: #9a9a9a;
    --text-light: #e6e6e6;
  }
  * { box-sizing: border-box; margin: 0; padding: 0; }
  html, body {
    width: 1200px; height: 900px; overflow: hidden;
    background: var(--stage);
  }
  .stage {
    position: relative; width: 1200px; height: 900px;
    display: flex; flex-direction: column; align-items: center; justify-content: center; gap: 60px;
  }
  .card {
    position: relative; width: 560px; height: 320px;
    border-radius: 24px;
    box-shadow: 0 14px 34px rgba(0,0,0,.45);
    overflow: hidden;
    font-family: "Open Sans", sans-serif;
  }
  .company-name {
    font-family: "Open Sans", sans-serif;
    font-weight: 600;
    line-height: 1;
    white-space: nowrap;
  }

  /* back */
  .card-back { background: var(--card-dark); }
  .card-back .company-name {
    position: absolute; top: 128px; left: 0; right: 0;
    text-align: center; font-size: 30px; color: var(--text-light);
  }
  .card-back .rule {
    position: absolute; top: 186px; left: 80px; right: 80px;
    height: 1px; background: var(--rule-dark);
  }
  .card-back .web {
    position: absolute; top: 206px; left: 0; right: 0; text-align: center;
    font-size: 13px; letter-spacing: 4px; color: var(--text-light);
  }

  /* front */
  .card-front { background: var(--card-light); color: var(--ink); }
  .card-front .company-name {
    position: absolute; top: 70px; right: 36px; font-size: 28px; color: var(--ink-strong);
  }
  .card-front .rule-top {
    position: absolute; top: 116px; left: 196px; right: 36px;
    height: 1px; background: var(--rule-light);
  }
  .address {
    position: absolute; top: 150px; right: 36px; text-align: right;
    font-size: 14px; line-height: 1.35; font-style: normal;
  }
  .person { position: absolute; left: 32px; top: 170px; }
  .person .name {
    font-size: 17px; font-weight: 600; text-transform: uppercase;
    color: var(--accent); line-height: 1.2;
  }
  .person .role { font-size: 14px; margin-top: 1px; }
  .card-front .rule-mid {
    position: absolute; top: 222px; left: 32px; width: 300px;
    height: 1px; background: var(--rule-light);
  }
  .contacts { position: absolute; left: 32px; top: 234px; list-style: none; }
  .contacts li {
    display: flex; align-items: center; gap: 7px;
    font-size: 15px; line-height: 22px;
  }
  .contacts svg { width: 14px; height: 14px; fill: var(--accent); flex: none; }
</style>
</head>
<body>
<main class="stage">

  <section class="card card-back" aria-label="Card back">
    <div class="company-name">R Dove Paygrid Works LLC.</div>
    <div class="rule"></div>
    <div class="web">www.dovepaygrid.net</div>
  </section>

  <section class="card card-front" aria-label="Card front">
    <div class="company-name">R Dove Paygrid Works LLC.</div>
    <div class="rule-top"></div>

    <address class="address">
      27, Nizami Street Block B<br>
      Baku, Azerbaijan 1010
    </address>

    <div class="person">
      <div class="name">Elias Morrow</div>
      <div class="role">Managing Director</div>
    </div>
    <div class="rule-mid"></div>

    <ul class="contacts">
      <li>
        <svg viewBox="0 0 16 16" aria-hidden="true"><path d="M1 6c0-2 3-4 7-4s7 2 7 4v1h-4V5.5C10 5 9 5 8 5s-2 0-3 .5V7H1zM3 9h10l1 5H2z"/></svg>
        055-310 742 618
      </li>
      <li>
        <svg viewBox="0 0 16 16" aria-hidden="true"><path d="M4.5 1h7a1 1 0 0 1 1 1v12a1 1 0 0 1-1 1h-7a1 1 0 0 1-1-1V2a1 1 0 0 1 1-1zm1 2v8h5V3zm2.5 9.2a.9.9 0 1 0 0 1.8.9.9 0 0 0 0-1.8z"/></svg>
        055-310 742 618
      </li>
      <li>
        <svg viewBox="0 0 16 16" aria-hidden="true"><path d="M1 3h14v1.2L8 9 1 4.2zm0 2.6 7 4.8 7-4.8V13H1z"/></svg>
        hello@dovepaygrid.net
      </li>
    </ul>
  </section>

</main>
</body>
</html>
```